Corvane Card

The logo is the Spanish flag colors I want a vibrant eye catching design with the yellow / red colors over either Navy or white background or black even ,
Would like a 2D feel to the logo with another lighter color logo under it look ,

Contact Information for Business Card

Corvane Flooring
Teodor Vashkin
Main Number
Cell Number
Fax Number

Website on the side of the card somewhere

Font styles to use
Sans Serif

Colors
ec1f27
ffc214

Requirements
Must have
• 2 logos feel one is bolder and the other one underneath very light

```html
<!DOCTYPE html>
<html lang="en">
<head>
<meta charset="utf-8">
<title>Corvane Flooring – Business Card</title>
<link href="https://fonts.googleapis.com/css2?family=Montserrat:wght@300;700&display=swap" rel="stylesheet">
<style>
  :root {
    --sun: #ffc418;
    --red: #ec1f27;
    --red-soft: #f1545a;
    --navy: #10153f;
    --white: #ffffff;
    --ink: #1c1c1c;
    --shadow: rgba(120, 80, 0, 0.28);
  }
  * { margin: 0; padding: 0; box-sizing: border-box; }
  html, body {
    width: 999px; height: 1200px; overflow: hidden;
    background: var(--sun);
    font-family: "Montserrat", Arial, sans-serif;
  }
  .canvas { position: relative; width: 999px; height: 1200px; }
  .card {
    position: absolute; left: 71px; width: 845px; height: 483px;
    box-shadow: 10px 14px 28px var(--shadow);
    overflow: hidden;
  }
  .card--front { top: 90px; background: var(--white); }
  .card--back { top: 622px; background: var(--navy); }

  .brand {
    position: absolute; display: flex; align-items: center;
    font-weight: 700; color: var(--sun); text-transform: uppercase;
    white-space: nowrap;
  }
  .brand__mark { display: block; background: var(--red); }
  .card--front .brand { right: 56px; top: 100px; font-size: 16px; letter-spacing: 2px; gap: 10px; }
  .card--front .brand__mark { width: 16px; height: 16px; }
  .card--back .brand {
    left: 0; right: 0; top: 205px; justify-content: center;
    font-size: 32px; letter-spacing: 5px; gap: 18px;
  }
  .card--back .brand__mark { width: 30px; height: 30px; }

  .person { position: absolute; left: 72px; top: 163px; }
  .person__name { font-weight: 700; font-size: 50px; color: var(--red); line-height: 1; letter-spacing: -0.5px; }
  .person__role { font-weight: 300; font-size: 25px; color: var(--ink); margin-top: 6px; }

  .contact-band {
    position: absolute; left: 0; bottom: 0; width: 100%; height: 209px;
    background: var(--red);
  }
  .contact {
    position: absolute; top: 54px; width: 220px; margin-left: -110px;
    text-align: center; color: var(--white);
  }
  .contact--main { left: 134px; }
  .contact--cell { left: 408px; }
  .contact--fax { left: 682px; }
  .contact__icon { display: block; margin: 0 auto; height: 34px; }
  .contact__number { font-weight: 300; font-size: 20px; margin-top: 16px; letter-spacing: 0.2px; }
  .contact--cell .contact__number { margin-top: 18px; }
  .divider {
    position: absolute; top: 75px; width: 2px; height: 40px; background: var(--red-soft);
  }
  .divider--one { left: 260px; }
  .divider--two { left: 550px; }

  .website {
    position: absolute; left: 0; right: 0; top: 405px; text-align: center;
    font-weight: 300; font-size: 20px; color: var(--sun); letter-spacing: 0.3px;
  }
</style>
</head>
<body>
<main class="canvas">
  <section class="card card--front">
    <div class="brand"><span class="brand__mark"></span>Corvane Flooring</div>
    <div class="person">
      <h1 class="person__name">Teodor Vashkin</h1>
      <p class="person__role">Owner</p>
    </div>
    <div class="contact-band">
      <div class="contact contact--main">
        <svg class="contact__icon" viewBox="3 2 16 16" width="34" aria-label="Main number">
          <path fill="#fff" d="M6.6 2.5c.6-.3 1.3-.1 1.6.5l1.3 2.6c.3.6.1 1.2-.4 1.6l-1.2.9c.9 2 2.6 3.8 4.6 4.8l1-1.2c.4-.5 1.1-.6 1.6-.3l2.6 1.4c.6.3.8 1 .5 1.6l-.8 1.6c-.5 1-1.7 1.4-2.8 1C9 15.6 5.2 11.6 3.8 6.2c-.3-1 .1-2.1 1.1-2.6z"/>
        </svg>
        <p class="contact__number">555 010 0100</p>
      </div>
      <span class="divider divider--one"></span>
      <div class="contact contact--cell">
        <svg class="contact__icon" viewBox="0 0 14 24" width="21" aria-label="Cell number">
          <rect x="1" y="1" width="12" height="22" rx="2" fill="#fff"/>
          <rect x="3" y="3.5" width="8" height="13" fill="var(--red)"/>
          <circle cx="7" cy="19.5" r="1.3" fill="var(--red)"/>
        </svg>
        <p class="contact__number">555 010 0200</p>
      </div>
      <span class="divider divider--two"></span>
      <div class="contact contact--fax">
        <svg class="contact__icon" viewBox="0 0 26 26" width="28" aria-label="Fax number">
          <rect x="1" y="9" width="4" height="15" rx="1" fill="#fff"/>
          <path fill="#fff" d="M7 9h2V3h10l3 3v3h1a1 1 0 0 1 1 1v13a1 1 0 0 1-1 1H8a1 1 0 0 1-1-1z"/>
          <rect x="11" y="5" width="8" height="5" fill="var(--red)"/>
          <g fill="var(--red)">
            <rect x="11" y="13" width="2.5" height="2.5"/><rect x="16" y="13" width="2.5" height="2.5"/>
            <rect x="11" y="18" width="2.5" height="2.5"/><rect x="16" y="18" width="2.5" height="2.5"/>
          </g>
        </svg>
        <p class="contact__number">555 010 0300</p>
      </div>
    </div>
  </section>

  <section class="card card--back">
    <div class="brand"><span class="brand__mark"></span>Corvane Flooring</div>
    <p class="website">www.website.com</p>
  </section>
</main>
</body>
</html>
```